Oil and Gas Exploration and Production company needs a business card design

We need a business card design using our logo and colors in the logo. We want a mainstream design.

```html
<!DOCTYPE html>
<html lang="en">
<head>
<meta charset="utf-8">
<title>Kestrel Oil &amp; Gas – Business Card</title>
<link href="https://fonts.googleapis.com/css2?family=Lato:wght@400;700;900&display=swap" rel="stylesheet">
<style>
  :root {
    --gold: #c99a2e;
    --ink: #111111;
    --text-grey: #555555;
    --card: #ffffff;
    --page: #f2f2f2;
  }
  * { margin: 0; padding: 0; box-sizing: border-box; }
  html, body {
    width: 1200px;
    height: 1200px;
    overflow: hidden;
    background: var(--page);
    font-family: "Lato", sans-serif;
  }
  .card {
    position: absolute;
    left: 60px;
    top: 292px;
    width: 1080px;
    height: 615px;
    background: var(--card);
    border-radius: 40px;
    overflow: hidden;
  }
  .brand {
    position: absolute;
    left: 490px;
    top: 80px;
    display: flex;
    align-items: center;
    gap: 22px;
    color: var(--ink);
    font-weight: 900;
  }
  .brand-dot {
    width: 66px;
    height: 66px;
    border-radius: 50%;
    background: var(--gold);
    flex: none;
  }
  .brand-name {
    display: flex;
    flex-direction: column;
    line-height: 1;
  }
  .brand-name .primary { font-size: 104px; letter-spacing: -1px; }
  .brand-name .secondary { font-size: 40px; letter-spacing: 9px; margin-top: 8px; }
  .accent-tab {
    position: absolute;
    left: 0;
    top: 282px;
    width: 40px;
    height: 112px;
    background: var(--gold);
    border-radius: 0 56px 56px 0;
  }
  .person {
    position: absolute;
    left: 59px;
    top: 294px;
  }
  .person-name {
    font-size: 42px;
    font-weight: 700;
    color: var(--ink);
    line-height: 1.1;
  }
  .person-title {
    font-size: 25px;
    font-weight: 700;
    color: var(--gold);
    margin-top: 10px;
  }
  .contacts {
    position: absolute;
    left: 60px;
    top: 450px;
    list-style: none;
    font-size: 25px;
    color: var(--text-grey);
  }
  .contacts li {
    display: flex;
    align-items: center;
    height: 38px;
  }
  .contacts svg {
    width: 20px;
    height: 20px;
    margin-right: 16px;
    fill: var(--gold);
  }
  .contacts .highlight { color: var(--gold); }
  .address {
    position: absolute;
    left: 459px;
    top: 488px;
    font-size: 25px;
    color: var(--text-grey);
    line-height: 38px;
  }
</style>
</head>
<body>
  <div class="card">
    <div class="brand">
      <span class="brand-dot"></span>
      <div class="brand-name">
        <span class="primary">Kestrel</span>
        <span class="secondary">OIL &amp; GAS</span>
      </div>
    </div>

    <div class="accent-tab"></div>
    <div class="person">
      <div class="person-name">Daniel Harper</div>
      <div class="person-title">President</div>
    </div>

    <ul class="contacts">
      <li>
        <svg viewBox="0 0 24 24" aria-hidden="true"><path d="M6.6 10.8a15.1 15.1 0 0 0 6.6 6.6l2.2-2.2c.3-.3.7-.4 1-.2 1.1.4 2.3.6 3.6.6.6 0 1 .4 1 1V20c0 .6-.4 1-1 1A17 17 0 0 1 3 4c0-.6.4-1 1-1h3.5c.6 0 1 .4 1 1 0 1.3.2 2.5.6 3.6.1.3 0 .7-.2 1z"/></svg>
        (08) 5550 1742
      </li>
      <li>
        <svg viewBox="0 0 24 24" aria-hidden="true"><path d="M2 5h20v14H2z M2 5l10 8 10-8" fill="var(--gold)"/><path d="M3 6l9 7 9-7" fill="none" stroke="#fff" stroke-width="1.6"/></svg>
        hello@kestreloil.com
      </li>
      <li>
        <svg viewBox="0 0 24 24" aria-hidden="true"><circle cx="12" cy="12" r="9.5" fill="none" stroke="var(--gold)" stroke-width="1.8"/><ellipse cx="12" cy="12" rx="4" ry="9.5" fill="none" stroke="var(--gold)" stroke-width="1.5"/><path d="M2.5 12h19M4 7.5h16M4 16.5h16" stroke="var(--gold)" stroke-width="1.5"/></svg>
        <span>www.<span class="highlight">kestreloil</span>.com</span>
      </li>
    </ul>

    <div class="address">
      Unit 4/52 Kessel Rd<br>
      Portmere SA 5790
    </div>
  </div>
</body>
</html>
```